Luxury Toilet Rental Business. Tallowby Hire.

Tallowby Hire (the logo is in the uploaded files)
We RENT and SELL Luxury Trailer toilets.
- Show location, number, pricing, pictures.
- We have two stall trailers for rent AND 3 stall trailers
- We sell them too
- We want our phone number shown
- We are a local company
- Slogan: Brighten your gathering with Tallowby Hire. The Velvet Privy
- We want a pricing portion
- We want the sizes shown
- We want the different rates/ prices shown
- We do 1 day rentals
- We do 1 week rentals
- We want the service area. We serve Los Angeles County, Orange County, Riverside County, San Bernardino County, and Palm Desert.
- Our location is in Marrow Creek California

Target Market(s)

Event planners, wedding planners, venue planners, concerts, events, gatherings.

Industry/Entity Type

Luxury Toilet Rentals

Number of Pages Required

1 page

Font styles to use
Serif
Sans Serif

Colors
EE7325
F08F49
F5BC92
FAE3D3
FDF4ED

Requirements
Must have
• Location, pricing, pictures, available areas. Our slogan.
Nice to have
• I like the idea of having tabs that show price, a tab that shows our contact information, pictures, event ideas, and where we service (the areas we'll go to)

```html
<!DOCTYPE html>
<html lang="en">
<head>
<meta charset="utf-8">
<title>Tallowby Hire – Luxury Trailer Toilets</title>
<link href="https://fonts.googleapis.com/css2?family=Michroma&family=Poppins:wght@400;500;600&display=swap" rel="stylesheet">
<style>
:root{
  --orange:#EE7325;
  --orange-mid:#F08F49;
  --peach:#F5BC92;
  --cream:#FAE3D3;
  --ivory:#FDF4ED;
  --ink:#111111;
  --text:#444444;
  --grey-band:#f2efec;
  --footer:#0b0b0b;
  --head:"Michroma",sans-serif;
  --body:"Poppins",sans-serif;
}
*{box-sizing:border-box;margin:0;padding:0}
html,body{width:1200px;height:4367px;overflow:hidden}
body{position:relative;font-family:var(--body);color:var(--text);background:#fff}
.abs{position:absolute}
.h2{font-family:var(--head);font-size:28px;font-weight:400;color:var(--ink);letter-spacing:1px;text-transform:uppercase;white-space:nowrap}
.h2 span{color:var(--orange)}
.rule{position:absolute;width:60px;height:4px;background:var(--orange)}
.btn{position:absolute;display:flex;align-items:center;justify-content:center;background:var(--orange);color:#fff;font-size:15px;border-radius:3px}

/* header */
.topline{left:0;top:0;width:1200px;height:4px;background:var(--orange)}
.phone-tab{left:797px;top:0;width:301px;height:40px;background:var(--orange);clip-path:polygon(0 0,100% 0,92% 100%,8% 100%);color:#fff;display:flex;align-items:center;justify-content:center;gap:10px;font-size:16px}
.brand{display:flex;align-items:center;gap:10px;font-family:var(--head);color:var(--orange);font-size:22px;white-space:nowrap}
.brand i{display:block;width:22px;height:22px;background:var(--orange)}
.nav{top:62px;left:376px;font-size:13px;font-weight:500;color:#222;letter-spacing:.5px}
.nav span{position:absolute;white-space:nowrap}

/* hero */
.hero{left:0;top:98px;width:1200px;height:597px;background:linear-gradient(180deg,#5a5c5e 0%,#6f706c 45%,#3f3e3a 100%)}
.hero-band{left:0;top:695px;width:1200px;height:13px;background:#e4e2e0}
.hero-title{left:0;width:1200px;top:264px;text-align:center;font-family:var(--head);font-size:36px;line-height:59px;color:#fff;font-weight:400;text-transform:uppercase;white-space:nowrap}
.hero-title em{font-style:normal;color:var(--orange)}
.arrow-circ{position:absolute;width:30px;height:30px;border:2px solid #fff;border-radius:50%;display:flex;align-items:center;justify-content:center}

/* about */
.about-photo{left:98px;top:837px;width:467px;height:441px;border:6px solid var(--orange);border-radius:4px;background:linear-gradient(160deg,#c9c9c6,#8b8c8a 60%,#6c6f6c)}
.about-sub{left:632px;top:915px;font-family:var(--head);font-size:18px;color:var(--ink);white-space:nowrap}
.about-text{left:632px;top:954px;width:472px;font-size:15px;line-height:31px}

/* product */
.products{left:0;top:1393px;width:1200px;height:773px;background:var(--grey-band)}
.tab{position:absolute;height:47px;display:flex;align-items:center;justify-content:center;font-family:var(--head);font-size:15px;border-radius:3px}
.tab.on{background:var(--orange);color:#fff}
.tab.off{border:2px solid var(--orange);color:var(--orange)}
.card{position:absolute;background:#fff;border-radius:8px;box-shadow:0 4px 18px rgba(0,0,0,.06);text-align:center}
.card .ph{position:absolute;left:21px;top:19px;right:21px;height:193px;border-radius:8px;background:linear-gradient(180deg,#c9cdd3 0%,#9a9a96 55%,#b1b0ac 100%)}
.card h3{position:absolute;top:237px;width:100%;font-size:17px;font-weight:500;color:#111;letter-spacing:.5px}
.card .size{position:absolute;top:277px;width:100%;font-size:15px;color:#222}
.card .price{position:absolute;top:311px;width:100%;font-size:17px;color:var(--orange)}
.card .more{position:absolute;top:350px;width:100%;font-size:15px;color:#111}
.card .more span{border-bottom:1px solid #111}

/* service */
.area-img{position:absolute;top:2354px;width:232px;height:268px}
.area-label{position:absolute;top:2650px;width:250px;text-align:center;font-size:15px;font-weight:500;color:#111;letter-spacing:.5px}
.dark-circ{position:absolute;width:30px;height:30px;border:1.5px solid #333;border-radius:50%;display:flex;align-items:center;justify-content:center}

/* pricing */
.pricing{left:0;top:2770px;width:1200px;height:632px;background:linear-gradient(180deg,#f7e7dc,#f9ede4)}
.checks{left:98px;top:2962px;font-size:15px;color:#222;line-height:30px}
.checks div{display:flex;align-items:center;gap:14px}
.price-text{left:98px;top:3037px;width:310px;font-size:15px;line-height:31px}
.pcard{position:absolute;top:2895px;width:303px;height:403px;background:#fff;border-radius:6px;box-shadow:0 4px 20px rgba(0,0,0,.05)}
.pcard h4{position:absolute;top:50px;width:100%;text-align:center;font-size:14px;font-weight:600;color:#222}
.pcard .amt{position:absolute;top:90px;width:100%;text-align:center;font-family:var(--head);font-size:30px;color:var(--orange)}
.pcard ul{position:absolute;top:147px;left:36px;list-style:none;font-size:15px;color:#222}
.pcard li{display:flex;align-items:center;gap:14px;height:43px}
.pcard .all{position:absolute;top:322px;width:100%;text-align:center;font-size:16px;color:var(--orange)}
.pcard .all span{border-bottom:1px solid var(--orange)}

/* contact */
.field{position:absolute;background:#fff;border-radius:4px;box-shadow:0 2px 12px rgba(0,0,0,.08);font-size:13px;color:#555;padding:16px 17px}

/* footer */
.footer{left:0;top:3956px;width:1200px;height:411px;background:var(--footer);color:#fff}
.fhead{position:absolute;top:4025px;font-family:var(--head);font-size:20px;color:#fff;white-space:nowrap}
.flist{position:absolute;top:4062px;font-size:14px;line-height:31px;color:#fff}
.flist div{display:flex;align-items:center;gap:14px}
.social{position:absolute;top:4150px;width:30px;height:30px;border-radius:50%;background:var(--orange)}
.cicon{position:absolute;left:846px;width:38px;height:38px;border-radius:50%;background:var(--orange);display:flex;align-items:center;justify-content:center}
.ctext{position:absolute;left:897px;font-size:14px;line-height:24px;color:#fff}
</style>
</head>
<body>

<!-- Header -->
<div class="abs topline"></div>
<div class="abs phone-tab">
  <svg width="16" height="16" viewBox="0 0 24 24" fill="#fff"><path d="M6.6 10.8a15.1 15.1 0 006.6 6.6l2.2-2.2a1 1 0 011-.25 11.4 11.4 0 003.6.57 1 1 0 011 1V20a1 1 0 01-1 1A17 17 0 013 4a1 1 0 011-1h3.5a1 1 0 011 1c0 1.25.2 2.45.57 3.57a1 1 0 01-.25 1z"/></svg>
  +1 555 014 2290
</div>
<div class="abs brand" style="left:98px;top:38px"><i></i>Tallowby Hire</div>
<nav class="abs nav">
  <span style="left:0">HOME</span>
  <span style="left:90px">EVENTS</span>
  <span style="left:197px">GALLERY</span>
  <span style="left:312px">SERVICE AREAS</span>
  <span style="left:485px">PRICING</span>
  <span style="left:590px">CONTACT</span>
  <span style="left:706px;top:-3px"><svg width="20" height="20" viewBox="0 0 24 24" fill="none" stroke="#222" stroke-width="2"><circle cx="10" cy="10" r="7"/><path d="M15 15l6 6"/></svg></span>
</nav>

<!-- Hero -->
<section class="abs hero" role="img" aria-label="Grey luxury toilet trailer parked in front of a yellow brick building"></section>
<div class="abs hero-band"></div>
<h1 class="abs hero-title">Brighten your gathering with<br>Tallowby Hire. The<br><em>Velvet Privy</em></h1>
<div class="btn" style="left:519px;top:468px;width:162px;height:44px;font-family:var(--head);font-size:13px">GET STARTED</div>
<div class="arrow-circ" style="left:26px;top:381px"><svg width="12" height="12" viewBox="0 0 12 12" fill="none" stroke="#fff" stroke-width="1.6"><path d="M8 1L3 6l5 5"/></svg></div>
<div class="arrow-circ" style="left:1135px;top:381px"><svg width="12" height="12" viewBox="0 0 12 12" fill="none" stroke="#fff" stroke-width="1.6"><path d="M4 1l5 5-5 5"/></svg></div>

<!-- About -->
<div class="abs about-photo" role="img" aria-label="Grey two-axle toilet trailer with step jacks"></div>
<h2 class="abs h2" style="left:632px;top:830px">About <span>Us</span></h2>
<div class="rule" style="left:632px;top:879px"></div>
<div class="abs about-sub">We are a local company</div>
<p class="abs about-text">At vero eos et accusamus et iusto odio dignissimos ducimus qui blanditiis praesentium voluptatum deleniti atque corrupti quos dolores et quas molestias excepturi sint occaecati cupiditate non provident, similique sunt in culpa qui officia deserunt mollitia animi, id est laborum et dolorum fuga. Et harum quidem rerum facilis est et expedita distinctio. Nam libero tempore, cum soluta nobis est eligendi optio cumque omnis dolor repellendus.</p>
<div class="btn" style="left:632px;top:1227px;width:131px;height:46px">Read More</div>

<!-- Products -->
<section class="abs products"></section>
<h2 class="abs h2" style="left:0;width:1200px;text-align:center;top:1488px">Our <span>Product</span></h2>
<div class="rule" style="left:570px;top:1540px"></div>
<div class="tab on" style="left:459px;top:1578px;width:131px">RENT</div>
<div class="tab off" style="left:607px;top:1578px;width:135px">SELL</div>
<article class="card" style="left:115px;top:1671px;width:471px;height:400px">
  <div class="ph" role="img" aria-label="Two stall toilet trailer with fold-out steps"></div>
  <h3>TWO STALL TRAILERS</h3>
  <div class="size">SIZE: 123</div>
  <div class="price">PRICE: $23.00</div>
  <div class="more"><span>VIEW MORE</span></div>
</article>
<article class="card" style="left:612px;top:1671px;width:473px;height:400px">
  <div class="ph" role="img" aria-label="Three stall toilet trailer with blue steps"></div>
  <h3>3 STALL TRAILERS</h3>
  <div class="size">SIZE: 123</div>
  <div class="price">PRICE: $23.00</div>
  <div class="more"><span>VIEW MORE</span></div>
</article>

<!-- Service area -->
<h2 class="abs h2" style="left:0;width:1200px;text-align:center;top:2260px">Service <span>Area</span></h2>
<div class="rule" style="left:570px;top:2310px"></div>
<div class="area-img" style="left:98px;background:linear-gradient(180deg,#8ab4cf,#d8c59a 50%,#5e7a55)" role="img" aria-label="Desert oasis with palm trees, Palm Desert"></div>
<div class="area-img" style="left:356px;background:linear-gradient(180deg,#a8c1d8,#b79a83 45%,#6f7f5a)" role="img" aria-label="Aerial view of Riverside County town"></div>
<div class="area-img" style="left:614px;background:linear-gradient(180deg,#f2a03a,#e0742a 40%,#2a2420)" role="img" aria-label="Palm trees at sunset on an Orange County beach"></div>
<div class="area-img" style="left:871px;background:linear-gradient(180deg,#b9d2e6,#7f9aa8 40%,#4f6a48)" role="img" aria-label="Aerial view of Los Angeles County skyline"></div>
<div class="area-label" style="left:89px">PALM DESERT</div>
<div class="area-label" style="left:346px">RIVERSIDE COUNTY</div>
<div class="area-label" style="left:604px">ORANGE COUNTY</div>
<div class="area-label" style="left:866px">LOS ANGELES COUNTY</div>
<div class="dark-circ" style="left:31px;top:2492px"><svg width="12" height="12" viewBox="0 0 12 12" fill="none" stroke="#333" stroke-width="1.5"><path d="M8 1L3 6l5 5"/></svg></div>
<div class="dark-circ" style="left:1140px;top:2492px"><svg width="12" height="12" viewBox="0 0 12 12" fill="none" stroke="#333" stroke-width="1.5"><path d="M4 1l5 5-5 5"/></svg></div>

<!-- Pricing -->
<section class="abs pricing"></section>
<h2 class="abs h2" style="left:98px;top:2871px">Our <span>Pricing</span></h2>
<div class="rule" style="left:98px;top:2925px"></div>
<div class="abs checks">
  <div><svg width="15" height="15" viewBox="0 0 16 16" fill="none" stroke="#222" stroke-width="1.6"><rect x="1" y="2" width="12" height="12" rx="2"/><path d="M4 8l3 3 8-9"/></svg>We do 1 day rentals</div>
  <div><svg width="15" height="15" viewBox="0 0 16 16" fill="none" stroke="#222" stroke-width="1.6"><rect x="1" y="2" width="12" height="12" rx="2"/><path d="M4 8l3 3 8-9"/></svg>We do 1 week rentals</div>
</div>
<p class="abs price-text">At vero eos et accusamus et iusto odio dignissimos ducimus qui blanditiis praesentium voluptatum deleniti atque corrupti quos dolores et quas molestias excepturi sint occaecati cupiditate non provident</p>
<div class="btn" style="left:98px;top:3241px;width:132px;height:46px">Read More</div>

<article class="pcard" style="left:470px">
  <h4>WE DO 1 DAY RENTALS</h4>
  <div class="amt">$130.00</div>
  <ul>
    <li><svg width="15" height="15" viewBox="0 0 16 16" fill="none" stroke="#222" stroke-width="1.6"><rect x="1" y="2" width="12" height="12" rx="2"/><path d="M4 8l3 3 8-9"/></svg>Lorem ipsum dolor sit amet</li>
    <li><svg width="15" height="15" viewBox="0 0 16 16" fill="none" stroke="#222" stroke-width="1.6"><rect x="1" y="2" width="12" height="12" rx="2"/><path d="M4 8l3 3 8-9"/></svg>Lorem ipsum dolor sit amet</li>
    <li><svg width="15" height="15" viewBox="0 0 16 16" fill="none" stroke="#222" stroke-width="1.6"><rect x="1" y="2" width="12" height="12" rx="2"/><path d="M4 8l3 3 8-9"/></svg>Lorem ipsum dolor sit amet</li>
    <li><svg width="15" height="15" viewBox="0 0 16 16" fill="none" stroke="#222" stroke-width="1.6"><rect x="1" y="2" width="12" height="12" rx="2"/><path d="M4 8l3 3 8-9"/></svg>Lorem ipsum dolor sit amet</li>
  </ul>
  <div class="all"><span>View All</span></div>
</article>
<article class="pcard" style="left:797px">
  <h4>WE DO 1 WEEK RENTALS</h4>
  <div class="amt">$150.00</div>
  <ul>
    <li><svg width="15" height="15" viewBox="0 0 16 16" fill="none" stroke="#222" stroke-width="1.6"><rect x="1" y="2" width="12" height="12" rx="2"/><path d="M4 8l3 3 8-9"/></svg>Lorem ipsum dolor sit amet</li>
    <li><svg width="15" height="15" viewBox="0 0 16 16" fill="none" stroke="#222" stroke-width="1.6"><rect x="1" y="2" width="12" height="12" rx="2"/><path d="M4 8l3 3 8-9"/></svg>Lorem ipsum dolor sit amet</li>
    <li><svg width="15" height="15" viewBox="0 0 16 16" fill="none" stroke="#222" stroke-width="1.6"><rect x="1" y="2" width="12" height="12" rx="2"/><path d="M4 8l3 3 8-9"/></svg>Lorem ipsum dolor sit amet</li>
    <li><svg width="15" height="15" viewBox="0 0 16 16" fill="none" stroke="#222" stroke-width="1.6"><rect x="1" y="2" width="12" height="12" rx="2"/><path d="M4 8l3 3 8-9"/></svg>Lorem ipsum dolor sit amet</li>
  </ul>
  <div class="all"><span>View All</span></div>
</article>

<!-- Contact -->
<h2 class="abs h2" style="left:0;width:1200px;text-align:center;top:3496px">Contact <span>Us</span></h2>
<div class="rule" style="left:570px;top:3546px"></div>
<div class="field" style="left:181px;top:3598px;width:411px;height:48px">Name</div>
<div class="field" style="left:605px;top:3598px;width:412px;height:48px">Email</div>
<div class="field" style="left:181px;top:3661px;width:411px;height:48px">Phone Number</div>
<div class="field" style="left:605px;top:3661px;width:412px;height:48px">Subject</div>
<div class="field" style="left:181px;top:3724px;width:836px;height:85px">Message</div>
<div class="btn" style="left:531px;top:3832px;width:137px;height:50px;font-family:var(--head);font-size:15px">Submit</div>

<!-- Footer -->
<footer class="abs footer"></footer>
<div class="abs brand" style="left:98px;top:4060px;font-size:24px"><i style="width:24px;height:24px"></i>Tallowby Hire</div>
<div class="social" style="left:107px" aria-label="Social profile"></div>
<div class="social" style="left:155px" aria-label="Social profile"></div>
<div class="social" style="left:204px" aria-label="Social profile"></div>
<div class="social" style="left:253px" aria-label="Social profile"></div>

<div class="fhead" style="left:402px">Quick Links</div>
<div class="flist" style="left:402px">
  <div><svg width="13" height="12" viewBox="0 0 13 12" fill="none" stroke="#fff" stroke-width="2"><path d="M0 6h11M6 1l5 5-5 5"/></svg>Home</div>
  <div><svg width="13" height="12" viewBox="0 0 13 12" fill="none" stroke="#fff" stroke-width="2"><path d="M0 6h11M6 1l5 5-5 5"/></svg>Events</div>
  <div><svg width="13" height="12" viewBox="0 0 13 12" fill="none" stroke="#fff" stroke-width="2"><path d="M0 6h11M6 1l5 5-5 5"/></svg>Gallery</div>
  <div><svg width="13" height="12" viewBox="0 0 13 12" fill="none" stroke="#fff" stroke-width="2"><path d="M0 6h11M6 1l5 5-5 5"/></svg>Service areas</div>
  <div><svg width="13" height="12" viewBox="0 0 13 12" fill="none" stroke="#fff" stroke-width="2"><path d="M0 6h11M6 1l5 5-5 5"/></svg>Pricing</div>
  <div><svg width="13" height="12" viewBox="0 0 13 12" fill="none" stroke="#fff" stroke-width="2"><path d="M0 6h11M6 1l5 5-5 5"/></svg>Contact</div>
</div>

<div class="fhead" style="left:625px">Other Links</div>
<div class="flist" style="left:625px;top:4055px">
  <div><svg width="13" height="12" viewBox="0 0 13 12" fill="none" stroke="#fff" stroke-width="2"><path d="M0 6h11M6 1l5 5-5 5"/></svg>FAQ</div>
  <div><svg width="13" height="12" viewBox="0 0 13 12" fill="none" stroke="#fff" stroke-width="2"><path d="M0 6h11M6 1l5 5-5 5"/></svg>Terms of Use</div>
  <div><svg width="13" height="12" viewBox="0 0 13 12" fill="none" stroke="#fff" stroke-width="2"><path d="M0 6h11M6 1l5 5-5 5"/></svg>Privacy Policy</div>
  <div><svg width="13" height="12" viewBox="0 0 13 12" fill="none" stroke="#fff" stroke-width="2"><path d="M0 6h11M6 1l5 5-5 5"/></svg>Support Links</div>
  <div><svg width="13" height="12" viewBox="0 0 13 12" fill="none" stroke="#fff" stroke-width="2"><path d="M0 6h11M6 1l5 5-5 5"/></svg>Conditions</div>
</div>

<div class="fhead" style="left:846px">Contact Us</div>
<div class="cicon" style="top:4075px"><svg width="16" height="18" viewBox="0 0 16 20" fill="#fff"><path d="M8 0a8 8 0 00-8 8c0 6 8 12 8 12s8-6 8-12a8 8 0 00-8-8zm0 11a3 3 0 110-6 3 3 0 010 6z"/></svg></div>
<div class="ctext" style="top:4076px">Tallowby Hire,<br>Marrow Creek California</div>
<div class="cicon" style="top:4134px"><svg width="16" height="13" viewBox="0 0 20 16" fill="#fff"><path d="M0 2a2 2 0 012-2h16a2 2 0 012 2v.5l-10 6-10-6zm0 2.8l10 6 10-6V14a2 2 0 01-2 2H2a2 2 0 01-2-2z"/></svg></div>
<div class="ctext" style="top:4142px">info@tallowbyhire.com</div>
<div class="cicon" style="top:4193px"><svg width="15" height="15" viewBox="0 0 24 24" fill="#fff"><path d="M6.6 10.8a15.1 15.1 0 006.6 6.6l2.2-2.2a1 1 0 011-.25 11.4 11.4 0 003.6.57 1 1 0 011 1V20a1 1 0 01-1 1A17 17 0 013 4a1 1 0 011-1h3.5a1 1 0 011 1c0 1.25.2 2.45.57 3.57a1 1 0 01-.25 1z"/></svg></div>
<div class="ctext" style="top:4200px">+1 555 014 2290</div>

<div class="abs" style="left:98px;top:4293px;width:1004px;height:1px;background:#555"></div>
<div class="abs" style="left:0;width:1200px;top:4318px;text-align:center;font-size:14px;color:#fff">Copyrights@2024.Tallowby Hire.All Rights Reserved</div>

</body>
</html>
```